Existing Website Requiring new Pages

I have an existing word press website that was built using elementor.
Website: www.tallowcrestcare.com.au
I require the Vacancies page (https://www.tallowcrestcare.com.au/vacancies/) to be modified to display our new properties along with minor tweaks to how the information is presented.
The vacancies to be displayed are the exactly the same as those that are located on the homepage of QMR website (https://qmr.org.au/)
The new pages that link off the Vacancies tab will require custom design.
There are roughly 8 pages/properties to be incorporated. i wish for the design to be very similar to that displayed in the following link; https://www.polunda.com.au/vacancies/merrylands
Along with this the back end has not been updated for the last 3 years so it also requires some maintenance.
Website is in the disability industry and the custom pages will display information relative to Property Vacancies.
I have attached a ZIP file with some design guides, the information for each of the properties (which will need to be modified to show our business name Tallowcrest Care) and the example of how it is to look based off the Polunda website.
If you guys have any suggestions or ideas on how to make this more presentable or possible i'm open to your ideas.
Target Market(s)
People looking for SDA properties custom built for people with a disability
Industry/Entity Type
Disability
Coding
Coded - Design and coding required
Number of Pages Required
5+ page

```html
<!DOCTYPE html>
<html lang="en">
<head>
<meta charset="utf-8">
<title>Tallowcrest Care – Specialist Disability Accommodation</title>
<link href="https://fonts.googleapis.com/css2?family=Montserrat:wght@400;500;600&display=swap" rel="stylesheet">
<style>
:root{
  --orange:#fb8c4f;
  --orange-nav:#f98a4c;
  --purple:#7b63c9;
  --amber:#f9a83d;
  --ink:#2b2b2b;
  --muted:#555;
  --cream:#fdf1dc;
  --tag-sda-bg:#fbd7b8;
  --tag-sda-fg:#c0502a;
  --tag-il:#e0653a;
  --tag-sil:#b8391f;
  --map:#2d2d2f;
  --white:#fff;
}
*{box-sizing:border-box;margin:0;padding:0}
html,body{width:1200px;height:2876px;overflow:hidden}
body{position:relative;font-family:'Montserrat',sans-serif;color:var(--ink);background:var(--white)}
.abs{position:absolute}
.ph{position:absolute;display:block}

/* header */
.brand{left:69px;top:30px;width:100px;color:var(--purple);font-weight:500;font-size:17px;line-height:1.1;text-align:center;letter-spacing:.5px}
.brand small{display:block;font-size:9px;letter-spacing:2px;font-weight:500}
.brand.light{color:var(--white)}
.nav{top:50px;display:flex;gap:0;font-size:14px;color:#444}
.nav a{position:absolute;white-space:nowrap;color:inherit;text-decoration:none}
.nav .active{color:var(--orange-nav)}

/* hero */
.hero-left{left:0;top:116px;width:613px;height:666px;background:var(--orange);overflow:hidden}
.hero-photo{left:613px;top:116px;width:587px;height:666px;background:linear-gradient(160deg,#6e6a66,#4b4642 55%,#8a7a5c)}
.category{left:99px;top:105px;width:395px;height:190px;background:var(--purple);border-radius:14px;color:var(--white)}
.category h3{position:absolute;left:17px;top:24px;font-size:17px;font-weight:600}
.category ul{position:absolute;left:17px;top:66px;list-style:none;font-size:13.5px;font-weight:500}
.category li{height:30px}
.category .ph{left:202px;top:67px;width:178px;height:105px;border-radius:8px;background:linear-gradient(135deg,#e9e3d7,#b9a98a)}
.unit{top:416px;width:291px;height:200px;background:var(--white);border-radius:12px}
.unit h4{position:absolute;left:17px;top:17px;font-size:21px;font-weight:500;line-height:1.15}
.unit p{position:absolute;left:17px;top:76px;width:110px;font-size:13px;color:var(--muted);line-height:1.3}
.unit .ph{left:158px;top:16px;width:117px;height:167px;border-radius:8px;background:linear-gradient(160deg,#cfd3d8,#3b4660)}
.pill{position:absolute;height:46px;border-radius:23px;background:var(--purple);color:var(--white);font-size:14px;font-weight:500;display:flex;align-items:center;padding-left:20px}
.arrow{position:absolute;right:10px;top:50%;transform:translateY(-50%);width:26px;height:26px;border-radius:50%;background:var(--amber)}
.arrow svg{position:absolute;left:6px;top:6px}
.hero-title{left:647px;top:150px;width:540px;font-size:36px;font-weight:600;color:var(--white);line-height:1.15}
.hero-text{left:647px;top:242px;width:470px;font-size:13.5px;color:var(--white);line-height:1.25}
.discover{left:647px;top:302px;width:168px;height:53px;border-radius:27px;background:var(--white);font-size:14px;font-weight:500;display:flex;align-items:center;padding-left:20px}
.discover .arrow{width:32px;height:32px}
.discover .arrow svg{left:9px;top:9px}
.finder{left:647px;top:477px;width:291px;height:272px;background:var(--white);border-radius:12px}
.finder h3{position:absolute;left:17px;top:24px;font-size:17px;font-weight:600}
.finder p{position:absolute;left:17px;top:52px;width:240px;font-size:13px;color:var(--muted);line-height:1.25}
.chip{position:absolute;top:100px;height:26px;border-radius:13px;background:#e5e0f6;font-size:12px;padding:0 14px;display:flex;align-items:center;gap:6px}
.field{position:absolute;left:17px;top:140px;width:257px;height:50px;border-radius:8px;background:var(--cream);font-size:13px;color:#999;display:flex;align-items:center;padding-left:46px}
.field svg{position:absolute;left:16px;top:15px}

/* listings */
.listing{width:337px}
.listing .ph{left:0;top:0;width:337px;height:337px;border-radius:20px}
.tags{position:absolute;right:0;top:365px;display:flex;gap:10px}
.tag{height:33px;border-radius:6px;font-size:13px;font-weight:500;display:flex;align-items:center;justify-content:center;color:var(--white)}
.tag.sda{width:62px;background:var(--tag-sda-bg);color:var(--tag-sda-fg)}
.tag.il{width:46px;background:var(--tag-il)}
.tag.sil{width:54px;background:var(--tag-sil)}
.listing h3{position:absolute;left:0;top:412px;font-size:26px;font-weight:500}
.listing p{position:absolute;left:0;top:457px;width:337px;font-size:13.5px;line-height:1.25;color:#333}
.nav-dot{position:absolute;top:156px;width:26px;height:26px;border-radius:50%;background:var(--white);opacity:.85}
.nav-dot svg{position:absolute;left:6px;top:6px}

/* map */
.map{left:0;top:2067px;width:1200px;height:500px;background:radial-gradient(circle at 60% 40%,#3a3a3c,var(--map))}
.map-title{left:67px;top:2120px;font-size:36px;font-weight:600;color:var(--white);line-height:1.15}
.map-search{left:875px;top:2124px;width:258px;height:50px;border-radius:8px;background:var(--cream);font-size:13px;color:#999;padding-left:46px;display:flex;align-items:center}
.map-search svg{position:absolute;left:16px;top:15px}
.pin{width:106px;height:106px;border-radius:50%;border:5px solid var(--white)}
.pin.hot{border-color:var(--orange)}
.map-card{left:810px;top:2334px;width:323px;height:183px;background:var(--orange);border-radius:12px;overflow:hidden;color:var(--white)}
.map-card h4{position:absolute;left:17px;top:17px;font-size:21px;font-weight:600}
.map-card p{position:absolute;left:17px;top:52px;width:160px;font-size:13px;line-height:1.25}
.map-card .ph{left:190px;top:0;width:133px;height:183px;background:linear-gradient(160deg,#cfd3d8,#3b4660)}

/* footer */
.footer{left:0;top:2567px;width:1200px;height:309px;background:var(--orange);color:var(--white)}
.col{position:absolute;top:64px}
.col h5{font-size:17px;font-weight:500;margin-bottom:14px}
.col a{display:block;font-size:13px;color:var(--white);text-decoration:none;height:30px}
.newsletter{left:733px;top:92px;width:400px;height:65px;border-radius:10px;background:rgba(255,255,255,.25);border:1px solid rgba(255,255,255,.5)}
.newsletter span{position:absolute;left:17px;top:23px;font-size:14px;color:#ffe7d6}
.subscribe{position:absolute;right:10px;top:9px;width:120px;height:45px;border-radius:8px;background:var(--orange);font-size:14px;display:flex;align-items:center;justify-content:center}
.rule{left:67px;top:221px;width:1066px;height:1px;background:rgba(255,255,255,.55)}
.copy{left:67px;top:251px;font-size:13px}
.social{top:249px;width:22px;height:22px;border-radius:50%;border:2px solid var(--white)}
</style>
</head>
<body>

<header>
  <div class="abs brand">TALLOWCREST<small>CARE</small></div>
  <nav class="abs nav" style="left:0;width:1200px">
    <a href="#" style="left:613px">Home</a>
    <a href="#" style="left:675px">About Us</a>
    <a href="#" class="active" style="left:758px">What We Do
      <svg width="14" height="9" viewBox="0 0 14 9" style="margin-left:6px"><path d="M1 1l6 6 6-6" fill="none" stroke="currentColor" stroke-width="1.6"/></svg></a>
    <a href="#" style="left:892px">Referrals</a>
    <a href="#" style="left:972px">Feedback</a>
    <a href="#" style="left:1058px">Contact Us</a>
  </nav>
</header>

<section>
  <div class="abs hero-left">
    <div class="abs category">
      <h3>Category</h3>
      <ul>
        <li>→&nbsp; Fully Accessible</li>
        <li>Highly Physical Support</li>
        <li>Improved Liveability</li>
        <li>Robust</li>
      </ul>
      <span class="ph" role="img" aria-label="Bright open-plan apartment interior"></span>
    </div>

    <div class="abs unit" style="left:-140px">
      <span class="ph" role="img" aria-label="Dining room with round table" style="left:158px"></span>
    </div>
    <div class="abs unit" style="left:179px">
      <h4>Urban<br>House</h4>
      <p>Lorem ipsum dolor sit amet consectetur.</p>
      <div class="pill" style="left:17px;top:137px;width:128px">$120/mo<span class="arrow"><svg width="14" height="14" viewBox="0 0 14 14"><path d="M2 7h10M8 3l4 4-4 4" fill="none" stroke="#7b63c9" stroke-width="1.8"/></svg></span></div>
      <span class="ph" role="img" aria-label="Living room with navy sofa"></span>
    </div>
    <div class="abs unit" style="left:497px">
      <h4>Urban<br>House</h4>
      <p>Lorem ipsum dolor sit amet consectetur.</p>
      <div class="pill" style="left:17px;top:137px;width:128px">$120/mo<span class="arrow"></span></div>
    </div>
  </div>

  <div class="abs hero-photo" role="img" aria-label="Woman in a wheelchair working on a laptop in a modern kitchen"></div>
  <h1 class="abs hero-title">Specialist Disability Accommodation Properties</h1>
  <p class="abs hero-text">Tallowcrest Care offers Specialist Disability Accommodation (SDA) in urban areas throughout Sydney, ensuring convenient proximity to medical services and pharmacies.</p>
  <div class="abs discover">Discover Now<span class="arrow"><svg width="14" height="14" viewBox="0 0 14 14"><path d="M2 7h10M8 3l4 4-4 4" fill="none" stroke="#7b63c9" stroke-width="1.8"/></svg></span></div>

  <div class="abs finder">
    <h3>Find Nearby Properties</h3>
    <p>Lorem ipsum dolor sit amet consectetur.</p>
    <span class="chip" style="left:17px">2 Bedroom <svg width="8" height="5" viewBox="0 0 8 5"><path d="M1 1l3 3 3-3" fill="none" stroke="#333"/></svg></span>
    <span class="chip" style="left:130px">3 Bathroom <svg width="8" height="5" viewBox="0 0 8 5"><path d="M1 1l3 3 3-3" fill="none" stroke="#333"/></svg></span>
    <div class="field"><svg width="18" height="20" viewBox="0 0 18 20"><path d="M9 19s7-6.5 7-11A7 7 0 0 0 2 8c0 4.5 7 11 7 11z" fill="none" stroke="#999" stroke-width="1.4"/><circle cx="9" cy="8" r="2.5" fill="none" stroke="#999" stroke-width="1.4"/></svg>Sydney</div>
    <div class="pill" style="left:17px;top:203px;width:257px;height:53px;border-radius:27px;font-size:14px">Search Properties<span class="arrow" style="width:32px;height:32px"><svg width="14" height="14" viewBox="0 0 14 14" style="left:9px;top:9px"><path d="M2 7h10M8 3l4 4-4 4" fill="none" stroke="#7b63c9" stroke-width="1.8"/></svg></span></div>
  </div>
</section>

<section>
  <article class="abs listing" style="left:67px;top:866px">
    <span class="ph" role="img" aria-label="New two-storey house on red soil lot" style="background:linear-gradient(180deg,#7ba4cf 0%,#b9c9d6 35%,#9b8f84 55%,#c8683c 75%,#b5552d)"></span>
    <span class="nav-dot" style="left:15px"><svg width="14" height="14" viewBox="0 0 14 14"><path d="M12 7H2M6 3L2 7l4 4" fill="none" stroke="#333" stroke-width="1.8"/></svg></span>
    <span class="nav-dot" style="left:296px"><svg width="14" height="14" viewBox="0 0 14 14"><path d="M2 7h10M8 3l4 4-4 4" fill="none" stroke="#333" stroke-width="1.8"/></svg></span>
    <div class="tags"><span class="tag sda">SDA</span><span class="tag il">IL</span><span class="tag sil">SIL</span></div>
    <h3>Sydney NSW 2011</h3>
    <p>Lorem ipsum dolor sit amet consectetur. At consectetur libero lorem pretium quisque mauris risus diam.</p>
    <div class="pill" style="left:0;top:533px;width:133px">Detail<span class="arrow"><svg width="14" height="14" viewBox="0 0 14 14"><path d="M2 7h10M8 3l4 4-4 4" fill="none" stroke="#7b63c9" stroke-width="1.8"/></svg></span></div>
  </article>
  <article class="abs listing" style="left:431px;top:866px">
    <span class="ph" role="img" aria-label="Dark timber house with thatched roof and patio" style="background:linear-gradient(180deg,#b89a6c 0%,#9c8262 30%,#3a3d44 50%,#2e3036 80%,#4e8a3a)"></span>
    <span class="nav-dot" style="left:15px"><svg width="14" height="14" viewBox="0 0 14 14"><path d="M12 7H2M6 3L2 7l4 4" fill="none" stroke="#333" stroke-width="1.8"/></svg></span>
    <span class="nav-dot" style="left:249px"><svg width="14" height="14" viewBox="0 0 14 14"><path d="M2 7h10M8 3l4 4-4 4" fill="none" stroke="#333" stroke-width="1.8"/></svg></span>
    <div class="tags"><span class="tag sda">SDA</span><span class="tag il">IL</span><span class="tag sil">SIL</span></div>
    <h3>Sydney NSW 2011</h3>
    <p>Lorem ipsum dolor sit amet consectetur. At consectetur libero lorem pretium quisque mauris risus diam.</p>
  </article>
  <article class="abs listing" style="left:795px;top:866px">
    <span class="ph" role="img" aria-label="Brick and siding family home with garage" style="background:linear-gradient(180deg,#b8c6d8 0%,#5a5f6a 30%,#a98a72 55%,#6d8a4a 80%,#c9b99c)"></span>
    <div class="tags"><span class="tag sda">SDA</span><span class="tag il">IL</span><span class="tag sil">SIL</span></div>
    <h3>Sydney NSW 2011</h3>
    <p>Lorem ipsum dolor sit amet consectetur. At consectetur libero lorem pretium quisque mauris risus diam.</p>
  </article>

  <article class="abs listing" style="left:67px;top:1479px">
    <span class="ph" role="img" aria-label="New two-storey house on red soil lot" style="background:linear-gradient(180deg,#7ba4cf 0%,#b9c9d6 35%,#9b8f84 55%,#c8683c 75%,#b5552d)"></span>
    <div class="tags"><span class="tag sda">SDA</span><span class="tag il">IL</span><span class="tag sil">SIL</span></div>
    <h3>Sydney NSW 2011</h3>
    <p>Lorem ipsum dolor sit amet consectetur. At consectetur libero lorem pretium quisque mauris risus diam.</p>
  </article>
  <article class="abs listing" style="left:431px;top:1479px">
    <span class="ph" role="img" aria-label="Dark timber house with thatched roof and patio" style="background:linear-gradient(180deg,#b89a6c 0%,#9c8262 30%,#3a3d44 50%,#2e3036 80%,#4e8a3a)"></span>
    <div class="tags"><span class="tag sda">SDA</span><span class="tag il">IL</span><span class="tag sil">SIL</span></div>
    <h3>Sydney NSW 2011</h3>
    <p>Lorem ipsum dolor sit amet consectetur. At consectetur libero lorem pretium quisque mauris risus diam.</p>
  </article>
  <article class="abs listing" style="left:795px;top:1479px">
    <span class="ph" role="img" aria-label="Brick and siding family home with garage" style="background:linear-gradient(180deg,#b8c6d8 0%,#5a5f6a 30%,#a98a72 55%,#6d8a4a 80%,#c9b99c)"></span>
    <div class="tags"><span class="tag sda">SDA</span><span class="tag il">IL</span><span class="tag sil">SIL</span></div>
    <h3>Sydney NSW 2011</h3>
    <p>Lorem ipsum dolor sit amet consectetur. At consectetur libero lorem pretium quisque mauris risus diam.</p>
  </article>
</section>

<section>
  <div class="abs map" role="img" aria-label="Dark street map of nearby neighbourhoods"></div>
  <h2 class="abs map-title">Affordable Property<br>Near You</h2>
  <div class="abs map-search"><svg width="18" height="20" viewBox="0 0 18 20"><path d="M9 19s7-6.5 7-11A7 7 0 0 0 2 8c0 4.5 7 11 7 11z" fill="none" stroke="#999" stroke-width="1.4"/><circle cx="9" cy="8" r="2.5" fill="none" stroke="#999" stroke-width="1.4"/></svg>Sydney</div>
  <span class="abs pin" role="img" aria-label="Living room property thumbnail" style="left:124px;top:2263px;background:linear-gradient(135deg,#e8ddd0,#8c7460)"></span>
  <span class="abs pin hot" role="img" aria-label="Living room property thumbnail" style="left:529px;top:2170px;background:linear-gradient(135deg,#cfd3d8,#3b4660)"></span>
  <span class="abs pin" role="img" aria-label="Dining room property thumbnail" style="left:593px;top:2386px;background:linear-gradient(135deg,#eeeae4,#9a7c5a)"></span>
  <div class="abs map-card">
    <h4>Urban House</h4>
    <p>Lorem ipsum dolor sit amet consectetur.</p>
    <div class="pill" style="left:17px;top:121px;width:160px">$120/mo<span class="arrow"><svg width="14" height="14" viewBox="0 0 14 14"><path d="M2 7h10M8 3l4 4-4 4" fill="none" stroke="#7b63c9" stroke-width="1.8"/></svg></span></div>
    <span class="ph" role="img" aria-label="Living room with navy sofa"></span>
  </div>
</section>

<footer class="abs footer">
  <div class="abs brand light" style="top:66px">TALLOWCREST<small>CARE</small></div>
  <div class="col" style="left:246px"><h5>Links</h5><a href="#">Home</a><a href="#">About Us</a><a href="#">Contact</a></div>
  <div class="col" style="left:337px"><h5>Resource</h5><a href="#">News</a><a href="#">FAQ</a><a href="#">Partner</a></div>
  <div class="col" style="left:443px"><h5>Accomodation</h5><a href="#">Supported Independent Living (SIL)</a><a href="#">Specialist Disability Accomodation (SDA)</a><a href="#">Short Term Accomodation</a></div>
  <div class="col" style="left:733px"><h5>Subscribe to Our Newsletter</h5></div>
  <div class="abs newsletter"><span>Your Domain (example.com)</span><div class="subscribe">Subscribe</div></div>
  <div class="abs rule"></div>
  <p class="abs copy">© 2024 Tallowcrest Care. All rights reserved.</p>
  <span class="abs social" role="img" aria-label="Social link" style="left:992px"></span>
  <span class="abs social" role="img" aria-label="Social link" style="left:1032px"></span>
  <span class="abs social" role="img" aria-label="Social link" style="left:1072px"></span>
  <span class="abs social" role="img" aria-label="Social link" style="left:1112px"></span>
</footer>

</body>
</html>
```